Captivating packaging design for sports company.

We need a packaging design that encompasses our resistance bands workout set. Our focus is quality, convenience, and versatility. The design should be tailored to our broad array of customer across all paths. We would like the packaging to reflect our brand and product features such as: the LBS(weight) listed on each of the bands, convenience for travel and at home, highest quality, for all fitness levels, and free eBook. We'd also like to include a couple of our reviews on the packaging. Please refer to our listing on Varlo for additional information https://www.shopvarlo.com/Brisklane-Athletics-Resistance-Workout-Carrying/dp/K47TR2XMNQ/ref=sr_1_1?ie=UTF8&qid=1470453588&sr=8-1&keywords=brisklane+athletics+resistance+bands
Please reach out with additional questions for any further details. Thank you.
Target Market(s)
Sports, fitness, and health enthusiasts of all ages.
Industry/Entity Type
It Company
Look and feel
Each slider illustrates characteristics of the customer's brand and the style your logo design should communicate.

```html
<!DOCTYPE html>
<html lang="en">
<head>
<meta charset="utf-8">
<title>Brisklane Athletics Resistance Bands Packaging</title>
<link rel="stylesheet" href="https://fonts.googleapis.com/css2?family=Michroma&family=Archivo:wght@500&display=swap">
<style>
  :root {
    --stage: #d9d9d9;
    --pack-green: #c8d785;
    --pack-green-light: #e6ecc6;
    --berry: #a6607f;
    --ink: #161616;
    --white: #ffffff;
    --photo-dark: #2b2a24;
    --photo-mid: #6e6f58;
  }
  html, body {
    margin: 0;
    width: 1200px;
    height: 1200px;
    overflow: hidden;
    background: var(--stage);
  }
  .dieline {
    position: absolute;
    left: 140px;
    top: 200px;
    display: flex;
    height: 800px;
  }
  .panel {
    position: relative;
    height: 100%;
    background: var(--pack-green);
    overflow: hidden;
  }
  .side-panel {
    width: 270px;
    border-right: 1px solid rgba(0,0,0,0.08);
  }
  .front-panel {
    width: 650px;
    background: radial-gradient(circle at 30% 40%, var(--pack-green-light) 0%, var(--pack-green) 70%);
  }
  .brand {
    display: flex;
    align-items: center;
    gap: 10px;
    font-family: "Michroma", sans-serif;
    color: var(--ink);
  }
  .brand-dot {
    width: 28px;
    height: 28px;
    border-radius: 50%;
    background: var(--ink);
    flex: none;
  }
  .side-panel .brand {
    position: absolute;
    left: 28px;
    top: 70px;
    font-size: 14px;
    line-height: 1.2;
  }
  .front-panel .brand {
    position: absolute;
    right: 48px;
    top: 130px;
    font-size: 17px;
    line-height: 1.2;
  }
  .seal {
    position: absolute;
    left: 100px;
    top: 165px;
    width: 78px;
    height: 78px;
    border-radius: 50%;
    border: 2px solid var(--ink);
  }
  .box-contents {
    position: absolute;
    left: 0;
    width: 100%;
    top: 290px;
    text-align: center;
    font-family: "Michroma", sans-serif;
    font-size: 10.5px;
    line-height: 1.75;
    color: var(--ink);
    margin: 0;
    padding: 0;
    list-style: none;
  }
  .slogan {
    position: absolute;
    left: 30px;
    top: 470px;
    margin: 0;
    font-family: "Archivo", sans-serif;
    font-weight: 500;
    font-size: 50px;
    line-height: 1.05;
    letter-spacing: 2px;
    color: var(--ink);
  }
  .resistance-total {
    position: absolute;
    left: 20px;
    top: 650px;
    width: 210px;
    padding: 16px 10px;
    background: var(--berry);
    color: var(--white);
    text-align: center;
    font-family: "Michroma", sans-serif;
    font-size: 12px;
    line-height: 1.35;
  }
  .athlete-photo {
    position: absolute;
    left: 90px;
    top: 120px;
    width: 260px;
    height: 680px;
    background: linear-gradient(180deg, var(--photo-dark) 0%, var(--photo-mid) 45%, var(--photo-dark) 100%);
    border-radius: 120px 120px 20px 20px;
    opacity: 0.85;
  }
  .title-band {
    position: absolute;
    left: 250px;
    top: 290px;
    width: 400px;
    height: 150px;
    background: var(--berry);
    box-shadow: 0 6px 0 var(--ink);
    color: var(--white);
    font-family: "Michroma", sans-serif;
    padding: 30px 0 0 18px;
    box-sizing: border-box;
  }
  .title-eyebrow {
    display: block;
    font-size: 17px;
    letter-spacing: 1px;
  }
  .title-main {
    display: block;
    font-size: 34px;
    line-height: 1.1;
    font-weight: 400;
    margin-top: 4px;
  }
  .features {
    position: absolute;
    left: 385px;
    top: 495px;
    font-family: "Michroma", sans-serif;
    font-size: 13px;
    line-height: 1.9;
    color: var(--ink);
  }
  .features p { margin: 0 0 24px; }
  .features ul { margin: 0; padding: 0; list-style: none; }
</style>
</head>
<body>
  <main class="dieline">
    <section class="panel side-panel">
      <div class="brand"><span class="brand-dot"></span><span>BRISKLANE<br>ATHLETICS</span></div>
      <div class="seal" aria-hidden="true"></div>
      <ul class="box-contents">
        <li>IN THE BOX</li>
        <li>x1 YELLOW - 2-4LB</li>
        <li>x1 GREEN - 4-6LB</li>
        <li>x1 BLUE - 10-12LB</li>
        <li>x1 RED - 15-20LB</li>
        <li>x1 BLACK - 25-30LB</li>
        <li>CARRY CASE</li>
        <li>E-BOOK</li>
      </ul>
      <h2 class="slogan">TONE<br>BURN<br>BUILD</h2>
      <div class="resistance-total">UP TO 75LBS<br>OF TOTAL<br>RESISTANCE</div>
    </section>
    <section class="panel front-panel">
      <div class="athlete-photo" role="img" aria-label="Photo of an athlete training with a resistance band, holding a handle in each hand"></div>
      <div class="brand"><span class="brand-dot"></span><span>BRISKLANE<br>ATHLETICS</span></div>
      <h1 class="title-band">
        <span class="title-eyebrow">HIGH QUALITY</span>
        <span class="title-main">RESISTANCE<br>BANDS</span>
      </h1>
      <div class="features">
        <p>Brisklane Athletics<br>Resistance Band<br>Workout Set</p>
        <ul>
          <li>4 Colourful Bands</li>
          <li>Door Anchor</li>
          <li>2 Handles</li>
          <li>2 Ankle Straps</li>
          <li>Carrying Case</li>
        </ul>
      </div>
    </section>
  </main>
</body>
</html>
```